For Lease Sign to Attract National Retail Tenants

Attached is a logo design that was created by Pixel Harbor. I will like to develop a leasing sign that is 4 foot wide by 4 foot high or 4 feet wide and 6 feet high. I would like the sign to have a black background and use the colors that are in the logo. These will be signs that are placed in front of shopping centers and are often read by passing motorist so the sign must be simple, clean, very easy to read, distinctive, and have as few words as possible. It would be good if small amounts of bright green can be added as a boarder or ????? The text should be FOR LEASE, 415-738-2916, Rod Kellaway. I will want to also design cards and letter head around the same theme.

Target Market(s)

National retail tenants wanting to lease space in my shopping centers

Industry/Entity Type

Real Estate Development

Contact Information for Business Card

Tall Oak Holdings, LLC Rod Kellaway President & CEO 4127 Marlow Ave. Suite 308 La Jolla, CA 92037 415-738-2916 rodkellaway@quillpost.net

```html
<!DOCTYPE html>
<html lang="en">
<head>
<meta charset="utf-8">
<title>For Lease Signs – Tall Oak Holdings</title>
<link rel="stylesheet" href="https://fonts.googleapis.com/css2?family=Fira+Sans+Extra+Condensed:wght@600;700&family=Nunito+Sans:wght@700;800&display=swap">
<style>
  :root {
    --canvas: #ffffff;
    --sign-black: #231f20;
    --sign-white: #ffffff;
    --accent-green: #3bbd00;
    --brand-grey: #d2d2d2;
    --brand-red: #e01b22;
  }
  html, body {
    margin: 0;
    padding: 0;
    width: 1200px;
    height: 720px;
    overflow: hidden;
    background: var(--canvas);
  }
  .canvas {
    position: relative;
    width: 1200px;
    height: 720px;
  }
  .sign {
    position: absolute;
    background: var(--sign-black);
    color: var(--sign-white);
    text-align: center;
  }
  .sign > * {
    position: absolute;
    left: 0;
    right: 0;
    margin: 0;
    line-height: 1;
    white-space: nowrap;
  }
  .pointer { display: block; margin: 0 auto; }
  .pointer polygon { fill: var(--accent-green); }

  /* 4 x 4 ft sign */
  .sign--square {
    left: 135px; top: 266px; width: 380px; height: 378px;
    font-family: "Nunito Sans", sans-serif;
    font-weight: 800;
  }
  .sign--square .headline { top: 28px; font-size: 56px; letter-spacing: 0.5px; }
  .sign--square .pointer-wrap { top: 96px; }
  .sign--square .phone { top: 144px; font-size: 43px; }
  .sign--square .contact-name { top: 201px; font-size: 29px; }
  .sign--square .brand { top: 318px; font-size: 19px; }

  /* 4 x 6 ft sign */
  .sign--tall {
    left: 683px; top: 76px; width: 380px; height: 568px;
    font-family: "Fira Sans Extra Condensed", sans-serif;
    font-weight: 700;
  }
  .sign--tall .headline { top: 34px; font-size: 96px; }
  .sign--tall .pointer-wrap { top: 149px; }
  .sign--tall .phone { top: 224px; font-size: 66px; }
  .sign--tall .contact-name { top: 302px; font-size: 42px; font-weight: 600; }
  .sign--tall .brand { top: 488px; font-size: 34px; font-weight: 600; }

  .brand {
    color: var(--brand-grey);
    display: flex;
    align-items: center;
    justify-content: center;
    gap: 10px;
  }
  .brand-mark {
    display: inline-block;
    width: 0.6em;
    height: 0.6em;
    background: var(--brand-red);
  }
</style>
</head>
<body>
<main class="canvas">

  <section class="sign sign--square" aria-label="For lease sign, 4 by 4 feet">
    <h1 class="headline">FOR LEASE</h1>
    <div class="pointer-wrap">
      <svg class="pointer" width="128" height="32" viewBox="0 0 128 32" aria-hidden="true">
        <polygon points="0,0 128,0 64,32"/>
      </svg>
    </div>
    <p class="phone">415-738-2916</p>
    <p class="contact-name">Rod Kellaway</p>
    <p class="brand"><span class="brand-mark" aria-hidden="true"></span>Tall Oak Holdings, LLC</p>
  </section>

  <section class="sign sign--tall" aria-label="For lease sign, 4 by 6 feet">
    <h1 class="headline">FOR LEASE</h1>
    <div class="pointer-wrap">
      <svg class="pointer" width="162" height="50" viewBox="0 0 162 50" aria-hidden="true">
        <polygon points="0,0 162,0 81,50"/>
      </svg>
    </div>
    <p class="phone">415-738-2916</p>
    <p class="contact-name">Rod Kellaway</p>
    <p class="brand"><span class="brand-mark" aria-hidden="true"></span>Tall Oak Holdings, LLC</p>
  </section>

</main>
</body>
</html>
```